Coral Bay Pools New website

I currently operate a swimming pool service and repair business and looking for a re design for my website as it has been over 5 years since it was designed. current site is coralbaypoolslv.com

```html
<!DOCTYPE html>
<html lang="en">
<head>
<meta charset="utf-8">
<title>Coral Bay Pools</title>
<link href="https://fonts.googleapis.com/css2?family=Lato:ital,wght@0,400;0,700;1,400&family=Yellowtail&display=swap" rel="stylesheet">
<style>
:root{
  --bg:#1b1b1b;
  --bg-deep:#151515;
  --blue:#16a4e1;
  --orange:#f0a024;
  --gold:#f2a81d;
  --text:#f2f2f2;
  --muted:#d9d9d9;
}
*{margin:0;padding:0;box-sizing:border-box}
html,body{width:1200px;height:4584px;overflow:hidden;background:var(--bg)}
body{position:relative;font-family:"Lato",sans-serif;color:var(--text)}
.abs{position:absolute}
.btn{position:absolute;display:flex;align-items:center;justify-content:center;background:var(--blue);color:#fff;font-size:15px;letter-spacing:.3px;border-radius:26px;text-transform:uppercase}
.btn-gold{background:var(--gold)}
.script{font-family:"Yellowtail",cursive;font-weight:400;color:#fff}
.rule{position:absolute;height:3px;background:var(--blue)}
.photo{position:absolute;border-radius:12px}
.photo.framed{border:3px solid #fff}
.brand{display:flex;align-items:center;gap:10px;font-family:"Lato",sans-serif;font-weight:700;font-size:22px;color:#fff;white-space:nowrap}
.brand-dot{width:16px;height:16px;border-radius:50%;background:var(--blue)}

.site-header{left:0;top:0;width:1200px;height:148px;background:var(--bg)}
.nav-link{position:absolute;top:56px;font-size:17px;color:#fff;text-transform:uppercase}
.nav-link.active{color:var(--blue)}
.nav-logo{left:510px;top:48px}

.hero{left:0;top:148px;width:1200px;height:660px}
.hero-title{left:0;width:1200px;top:320px;text-align:center;font-size:70px}
.hero-sub{left:0;width:1200px;top:442px;text-align:center;font-size:20px;font-weight:700;letter-spacing:.2px}

.section-title{font-size:46px}
.about-tag{left:112px;top:972px;font-style:italic;font-size:15px;color:var(--orange)}
.about-copy{left:112px;top:1012px;width:452px;font-size:14.3px;line-height:26px;text-align:justify;color:var(--muted)}

.service-label{position:absolute;top:1797px;font-size:20px;color:#fff;display:flex;align-items:center;gap:12px}

.welcome-bg{left:0;top:2038px;width:1200px;height:780px}
.welcome-panel{left:134px;top:2136px;width:934px;height:392px;background:rgba(40,40,44,.72);border-radius:14px}
.welcome-copy{left:160px;top:2270px;width:880px;text-align:center;font-size:14.3px;line-height:26px;color:#f0f0f0}
.link{color:var(--orange)}

.why-copy{left:641px;top:3810px;width:446px;font-size:14.3px;line-height:26px;text-align:justify;color:var(--muted)}

.footer-nav{left:112px;top:4320px;width:975px;height:59px;border-radius:30px;background:var(--blue)}
.footer-link{position:absolute;top:4340px;font-size:16px;color:#fff;text-transform:uppercase}
.social{position:absolute;top:4448px;width:40px;height:40px;border-radius:50%;background:var(--blue)}
.legal-bar{left:0;top:4552px;width:1200px;height:32px;background:var(--blue);display:flex;align-items:center;justify-content:center;font-size:13px;color:#fff}
</style>
</head>
<body>

<!-- Header -->
<header class="abs site-header">
  <span class="nav-link active" style="left:158px">Home</span>
  <span class="nav-link" style="left:244px">About</span>
  <span class="nav-link" style="left:336px">Our Services</span>
  <div class="abs brand nav-logo"><span class="brand-dot"></span>Coral Bay Pools</div>
  <span class="nav-link" style="left:728px;top:62px">Free Estimate</span>
  <span class="nav-link" style="left:886px;top:62px">Contact</span>
  <span class="btn" style="left:995px;top:48px;width:154px;height:46px">Get a Quote</span>
</header>

<!-- Hero -->
<section class="abs hero">
  <svg class="abs" style="left:0;top:0" width="1200" height="660" viewBox="0 0 1200 660">
    <defs>
      <linearGradient id="heroTone" x1="0" y1="0" x2="0" y2="1">
        <stop offset="0" stop-color="#4d4a47"/>
        <stop offset=".55" stop-color="#35403f"/>
        <stop offset="1" stop-color="#223035"/>
      </linearGradient>
    </defs>
    <rect width="1200" height="660" fill="url(#heroTone)" role="img" aria-label="Luxury home with curved pool and palm trees at dusk"/>
    <polygon points="0,520 855,636 1200,528 1200,660 0,660" fill="var(--bg)"/>
    <polygon points="0,524 855,640 1200,532 1200,546 855,650 0,540" fill="var(--blue)"/>
  </svg>
  <h1 class="abs script hero-title" style="top:170px">Reliable Pool Care, Done Right.</h1>
  <p class="abs hero-sub" style="top:294px">NEVADA'S HIGHEST RATED POOL CLEANING</p>
  <span class="btn" style="left:507px;top:356px;width:186px;height:48px">Free Estimate</span>
</section>

<!-- About -->
<section>
  <h2 class="abs script section-title" style="left:112px;top:870px">About Coral Bay Pools</h2>
  <div class="rule" style="left:148px;top:938px;width:226px"></div>
  <p class="abs about-tag">We are a full service pool company servicing the Las Vegas Valley.</p>
  <p class="abs about-copy">Hi There, My name is Marcus and I'm the owner of Coral Bay Pools. I recently started this business in 2016 to provide Las Vegas with excellent, reliable pool service. Just because we are a new company that doesn't mean we lack experience. I've been in the pool industry for seven years and counting and have managed everything from your backyard pool to olympic sized pools with five plus years managing casino properties as well.</p>
  <span class="btn" style="left:112px;top:1226px;width:244px;height:48px">Give Us a Call Today</span>
  <div class="photo" style="left:680px;top:892px;width:408px;height:363px;background:linear-gradient(180deg,#4a6fb8,#2f4a86 55%,#2a3a5a)" role="img" aria-label="Modern glass house with reflecting pool at twilight"></div>
  <div class="photo framed" style="left:621px;top:1082px;width:243px;height:211px;background:linear-gradient(180deg,#5b6270,#3a3f4a 50%,#1e2a4a)" role="img" aria-label="Desert home with lit pool at night"></div>
</section>

<!-- Services -->
<section>
  <h2 class="abs script section-title" style="left:0;width:1200px;text-align:center;top:1384px">Our Services</h2>
  <div class="rule" style="left:482px;top:1454px;width:236px"></div>
  <div class="photo framed" style="left:112px;top:1508px;width:316px;height:267px;background:linear-gradient(180deg,#6f86b0,#5a6272 50%,#2d4a4a)" role="img" aria-label="Modern stone home with pool at dusk"></div>
  <div class="photo" style="left:443px;top:1508px;width:314px;height:266px;background:linear-gradient(180deg,#e6e2da,#9fd6e3 55%,#27b1d8)" role="img" aria-label="Indoor pool with lounge chairs"></div>
  <div class="photo" style="left:775px;top:1508px;width:314px;height:266px;background:linear-gradient(180deg,#d98070,#7b6f9a 40%,#2b6fc6)" role="img" aria-label="Two storey home with infinity pool at sunset"></div>
  <span class="service-label" style="left:117px">Pool Services <svg width="22" height="14" viewBox="0 0 22 14"><path d="M1 7h19M14 1l6 6-6 6" fill="none" stroke="var(--orange)" stroke-width="2.2"/></svg></span>
  <span class="service-label" style="left:444px">Commercial Pools <svg width="22" height="14" viewBox="0 0 22 14"><path d="M1 7h19M14 1l6 6-6 6" fill="none" stroke="var(--orange)" stroke-width="2.2"/></svg></span>
  <span class="service-label" style="left:775px">Residential Pools <svg width="22" height="14" viewBox="0 0 22 14"><path d="M1 7h19M14 1l6 6-6 6" fill="none" stroke="var(--orange)" stroke-width="2.2"/></svg></span>
  <span class="btn" style="left:478px;top:1874px;width:244px;height:48px">View All Services</span>
</section>

<!-- Welcome -->
<section>
  <svg class="abs welcome-bg" width="1200" height="780" viewBox="0 0 1200 780">
    <defs>
      <linearGradient id="welcomeTone" x1="0" y1="0" x2="0" y2="1">
        <stop offset="0" stop-color="#2a2622"/>
        <stop offset=".5" stop-color="#2b3d4a"/>
        <stop offset=".8" stop-color="#5ea4c8"/>
        <stop offset="1" stop-color="#3b4a52"/>
      </linearGradient>
    </defs>
    <rect width="1200" height="780" fill="url(#welcomeTone)" role="img" aria-label="Backyard pool with cabana and lounge chairs lit at night"/>
    <polygon points="0,626 356,770 1200,626 1200,780 0,780" fill="var(--bg)"/>
    <polygon points="0,630 356,772 1200,630 1200,644 356,782 0,646" fill="var(--blue)"/>
  </svg>
  <div class="abs welcome-panel"></div>
  <h2 class="abs script section-title" style="left:0;width:1200px;text-align:center;top:2172px">Welcome</h2>
  <div class="rule" style="left:500px;top:2238px;width:218px"></div>
  <p class="abs welcome-copy">When you need professional pool cleaning services in Nevada, you can count on the professionals at Coral Bay Pools to provide you with superior and prompt solutions. Whether you need assistance with a <span class="link">residential</span> or <span class="link">commercial</span> pool, we'll vacuum, brush, and thoroughly clean your pool so it's swim-ready. We'll also clean your pool filters and inform you of any issues that arise. Our staff is certified by the Desert Valley Health Board to ensure proper chemical levels and equipment are safe. To learn more about our pool cleaning services or to get your <span class="link">free estimate</span>, contact our pool experts today.</p>
  <span class="btn" style="left:511px;top:2436px;width:178px;height:48px">Learn More</span>
</section>

<!-- Gallery -->
<section>
  <h2 class="abs script section-title" style="left:0;width:1200px;text-align:center;top:2890px">Our Gallery</h2>
  <div class="rule" style="left:478px;top:2968px;width:238px"></div>
  <div class="photo" style="left:112px;top:3024px;width:226px;height:217px;background:linear-gradient(180deg,#7d93bb,#5d6370 55%,#2d4648)" role="img" aria-label="Stone home with pool at dusk"></div>
  <div class="photo" style="left:112px;top:3257px;width:226px;height:205px;background:linear-gradient(180deg,#5d6470,#3a3e48 50%,#1e2a4a)" role="img" aria-label="Desert home with lit pool"></div>
  <div class="photo framed" style="left:352px;top:3024px;width:325px;height:440px;background:linear-gradient(180deg,#4a6fb8,#2f4a86 50%,#2a3a5a)" role="img" aria-label="Modern glass house with reflecting pool"></div>
  <div class="photo" style="left:692px;top:3024px;width:396px;height:205px;background:linear-gradient(180deg,#8a6a4a,#cfc3b2 45%,#2f6fa6)" role="img" aria-label="Pool with spa and stone patio"></div>
  <div class="photo" style="left:692px;top:3249px;width:159px;height:214px;background:linear-gradient(180deg,#e6e2da,#9fd6e3 55%,#27b1d8)" role="img" aria-label="Indoor pool with lounge chairs"></div>
  <div class="photo" style="left:869px;top:3249px;width:219px;height:214px;background:linear-gradient(180deg,#d98070,#7b6f9a 40%,#2b6fc6)" role="img" aria-label="Home with infinity pool at sunset"></div>
  <span class="btn btn-gold" style="left:497px;top:3520px;width:197px;height:48px">View Gallery</span>
</section>

<!-- Why choose us -->
<section>
  <div class="photo" style="left:169px;top:3708px;width:409px;height:356px;background:linear-gradient(180deg,#3a5a90,#6b5a48 45%,#34b6d8)" role="img" aria-label="Lit modern home with turquoise pool"></div>
  <div class="photo framed" style="left:112px;top:3667px;width:243px;height:207px;background:linear-gradient(180deg,#9bb0c6,#7b6a5a 40%,#2f7fd0)" role="img" aria-label="Two storey home with pool and stepping stones"></div>
  <h2 class="abs script section-title" style="left:641px;top:3702px">Why Choose Us?</h2>
  <div class="rule" style="left:660px;top:3768px;width:242px"></div>
  <p class="abs why-copy">Our full-service pool company proudly serves the entire Las Vegas valley, and we're certified by the Desert Valley Health Board to maintain the highest level of pool safety. If you need repairs, maintenance, scheduled cleanings, or any other pool services, contact us online or by phone today.</p>
  <span class="btn" style="left:640px;top:3972px;width:170px;height:48px">Contact Us</span>
</section>

<!-- Footer -->
<footer>
  <svg class="abs" style="left:0;top:4110px" width="1200" height="450" viewBox="0 0 1200 450">
    <defs>
      <linearGradient id="footerTone" x1="0" y1="0" x2="0" y2="1">
        <stop offset="0" stop-color="#2c3942"/>
        <stop offset=".5" stop-color="#1c2a36"/>
        <stop offset="1" stop-color="#121a22"/>
      </linearGradient>
    </defs>
    <rect y="10" width="1200" height="440" fill="url(#footerTone)" role="img" aria-label="Pool and patio at night"/>
    <polygon points="0,0 1200,0 1200,36 640,74 0,36" fill="var(--bg)"/>
    <polygon points="0,16 640,56 1200,16 1200,36 640,76 0,36" fill="var(--blue)"/>
  </svg>
  <div class="abs footer-nav"></div>
  <span class="footer-link" style="left:170px">Home</span>
  <span class="footer-link" style="left:247px">About Us</span>
  <span class="footer-link" style="left:352px">Our Services</span>
  <div class="abs brand" style="left:496px;top:4286px;background:var(--bg);padding:14px 20px;border-radius:14px"><span class="brand-dot"></span>Coral Bay Pools</div>
  <span class="footer-link" style="left:735px">Free Estimate</span>
  <span class="footer-link" style="left:874px">Contact</span>
  <span class="footer-link" style="left:977px">Blog</span>
  <span class="social" style="left:553px" role="img" aria-label="Social profile link"></span>
  <span class="social" style="left:604px" role="img" aria-label="Social profile link"></span>
  <div class="abs legal-bar">©2026 CORAL BAY POOLS - DO NOT DUPLICATE. ALL RIGHTS RESERVED.</div>
</footer>

</body>
</html>
```